Vibrant, yet professional, stationery set and other designs required.

I need to source a fantastic designer for a new project as part of my company using a new logo designed via sketch harbor.

**UPDATE** I am not looking for just 'fine' design that will suffice. I am looking for something great.

We are a life assurance brokerage based in Dublin, Ireland and BrightRoost.ie is our new website aimed at providing services for young families in Ireland. We are hoping to be the 'Velro' level of service providers in this area and I am looking for the quality of design to reflect this :-) Hopefully that makes sense!

I have a preference for straight lines over curves and waves.

I need...

1. Business card
2. Letterhead
3. Banner (for printing - 76cm X 305cm)
4. Car branding for KORVA 9 (2014 sport model) I believe the templates are freely available online.

Target Market(s)

Parents in Ireland - Aged 27 to 50.

Industry/Entity Type

Financial Planning

Colors

Designer to choose colors to be used in the design.

Requirements
Must have
• All of the items listed in the description above. I like clean, bright, legible, vibrant and professional design.
Should not have
• No silly or 'cheap' looking designs. This is a professional company looking to provide a professional service.

```html
<!DOCTYPE html>
<html lang="en">
<head>
<meta charset="utf-8">
<title>BrightRoost.ie – Business Card</title>
<link rel="stylesheet" href="https://fonts.googleapis.com/css2?family=Quicksand:wght@600&family=Roboto:wght@400&family=Roboto+Condensed:wght@500&display=swap">
<style>
  :root {
    --backdrop: #a3a3a3;
    --orange: #ef8119;
    --green: #9bc53d;
    --blue: #6cc5e3;
    --card-white: #f4f4f4;
    --logo-grey: #7d8a8e;
    --text-grey: #555a5c;
    --title-grey: #8a8f91;
    --white: #ffffff;
  }
  * { margin: 0; padding: 0; box-sizing: border-box; }
  html, body { width: 1200px; height: 960px; overflow: hidden; }
  body { background: var(--backdrop); position: relative; font-family: "Roboto", Arial, sans-serif; }

  .card { position: absolute; box-shadow: 0 2px 4px rgba(0,0,0,0.25); }

  /* Front */
  .card-front {
    left: 320px; top: 100px; width: 602px; height: 345px;
    background: var(--orange);
  }
  .card-front .brand {
    position: absolute; left: 0; right: 0; top: 130px;
    text-align: center; color: var(--white);
    font-family: "Quicksand", Arial, sans-serif; font-weight: 600; font-size: 50px;
    letter-spacing: -0.5px;
  }
  .card-front .web {
    position: absolute; left: 0; right: 0; top: 295px;
    text-align: center; color: var(--white);
    font-size: 14px; letter-spacing: 6px;
  }

  /* Back */
  .card-back {
    left: 320px; top: 493px; width: 600px; height: 342px;
    background: var(--card-white); overflow: hidden;
  }
  .card-back .brand {
    position: absolute; left: 32px; top: 48px;
    display: flex; align-items: center; gap: 8px;
    color: var(--logo-grey);
    font-family: "Quicksand", Arial, sans-serif; font-weight: 600; font-size: 34px;
  }
  .card-back .brand-dot { width: 12px; height: 12px; border-radius: 50%; background: var(--logo-grey); }
  .accent-bar { position: absolute; left: 0; top: 139px; width: 10px; height: 41px; background: var(--green); }
  .holder-name {
    position: absolute; left: 32px; top: 137px;
    font-family: "Roboto Condensed", Arial, sans-serif; font-weight: 500;
    font-size: 21px; color: var(--orange);
  }
  .holder-title { position: absolute; left: 32px; top: 164px; font-size: 14px; color: var(--title-grey); }
  .address { position: absolute; left: 32px; top: 192px; font-size: 14.5px; line-height: 19px; color: var(--text-grey); }
  .contacts { position: absolute; left: 32px; top: 234px; list-style: none; }
  .contacts li {
    display: flex; align-items: center; gap: 9px;
    height: 19.3px; font-size: 14.5px; color: var(--text-grey);
  }
  .contacts svg { width: 14px; height: 14px; fill: var(--orange); flex: none; }

  .family-figure-art {
    position: absolute; left: 320px; top: 15px; width: 242px; height: 327px;
    background: linear-gradient(90deg, var(--blue) 0%, var(--blue) 22%, var(--orange) 45%, var(--orange) 62%, var(--green) 82%, var(--green) 100%);
    opacity: 0.9;
  }
</style>
</head>
<body>

  <section class="card card-front">
    <div class="brand">BrightRoost.ie</div>
    <div class="web">www.brightroost.ie</div>
  </section>

  <section class="card card-back">
    <div class="brand"><span class="brand-name">BrightRoost.ie</span><span class="brand-dot"></span></div>
    <div class="accent-bar"></div>
    <div class="holder-name">AIDAN KEANE</div>
    <div class="holder-title">CEO/FOUNDER</div>
    <div class="address">14 Larkfield Row<br>Dublin, Ireland D06 K2R7</div>
    <ul class="contacts">
      <li><svg viewBox="0 0 16 16"><path d="M3.5 1.5l2.5 0 1 3.5-1.6 1.2a8 8 0 0 0 4.4 4.4L11 9l3.5 1v2.5c0 .8-.7 1.5-1.5 1.5C7 14 2 9 2 3c0-.8.7-1.5 1.5-1.5z"/></svg>601 482 7735</li>
      <li><svg viewBox="0 0 16 16"><path d="M5 1h6a1 1 0 0 1 1 1v12a1 1 0 0 1-1 1H5a1 1 0 0 1-1-1V2a1 1 0 0 1 1-1zm.5 2v9h5V3zM8 12.5a.8.8 0 1 0 0 1.6.8.8 0 0 0 0-1.6z"/></svg>873 519 2046</li>
      <li><svg viewBox="0 0 16 16"><path d="M4 1h8v4H4zM2 6h12a1 1 0 0 1 1 1v5h-2v3H3v-3H1V7a1 1 0 0 1 1-1zm3 5v3h6v-3z"/></svg>416 930 5812</li>
      <li><svg viewBox="0 0 16 16"><path d="M1 3h14v10H1zm1.5 1.2V5l5.5 4 5.5-4v-.8z"/></svg>hello@brightroost.ie</li>
      <li><svg viewBox="0 0 16 16"><path d="M8 1a7 7 0 1 0 0 14A7 7 0 0 0 8 1zm-1 2.2v2L5 7l1.5 2L6 12.5A5.5 5.5 0 0 1 7 3.2zm2.5.2A5.5 5.5 0 0 1 13 11l-2-1-1-2 1.5-2z"/></svg>www.brightroost.ie</li>
    </ul>
    <div class="family-figure-art" role="img" aria-label="Illustration of a family of three simple standing figures: a small blue child, a medium orange parent and a tall green parent"></div>
  </section>

</body>
</html>
```